Distribution/Printing company needs a web site to inform prospective customers on what we do.

Distribution/Printing/Packaging company needs a web site to inform prospective customers on what we do. Please look at our direct to consumer web site (under development) for an idea of the product lines we sell: storedev.maplewickhaven.com
Logo files are attached as is a flyer that is under development which contains other information about the company (this is to be used for content- not to be posted as is). The web site should be focused on our business customer base and is not intended to be direct to consumer. Site should have a link to our consumer web site.
Site design should be mobile friendly, or mobile could be redirected to a mobile version. This web site will be strictly informational and will not be designed for any sales transactions.

Target Market(s)

Manufacturing and retail businesses, any other multi-site business that would benefit from centralized pricing and budget controls we can provide (banks, medical/dental offices, educational facilities, etc).

Industry/Entity Type

It Company

Coding

Coded - Design and coding required

Number of Pages Required

5+ page

Requirements
Must have
• 1) Top level menu: Products, about us, locations, contact us, news
• 2) page with news/promotions that is easily updated
• 3) "contact us" form (name, company, phone, email address) email link
• 4) link to www.store.maplewickhaven.com with information that lower pricing is available for businesses
• 5) SEO keywords
• 6) Link to powerpoint presentation file
Nice to have
• 1) our phone number should appear on every page near the top

```html
<!DOCTYPE html>
<html lang="en">
<head>
<meta charset="utf-8">
<title>Maplewick Haven Supply – Packaging, Printing, Distribution</title>
<link rel="stylesheet" href="https://fonts.googleapis.com/css2?family=Raleway:wght@400;500;600&family=Open+Sans:wght@400;600;700&display=swap">
<style>
:root{
  --blue:#2a8ee8;
  --blue-dark:#1a6fc4;
  --blue-text:#2b8fdc;
  --ink:#222;
  --muted:#666;
  --grey-bg:#ececec;
  --line:#cfcfcf;
  --black:#050505;
  --white:#fff;
}
*{box-sizing:border-box;margin:0;padding:0}
html,body{width:1200px;height:2200px;overflow:hidden;background:var(--white)}
body{font-family:"Open Sans",sans-serif;color:var(--ink);position:relative}
.site-header{position:absolute;top:0;left:0;width:1200px;height:113px}
.brand{position:absolute;left:139px;top:20px;display:flex;align-items:center;gap:12px}
.brand-mark{width:22px;height:22px;background:var(--ink)}
.brand-name{font-family:"Open Sans",sans-serif;font-weight:700;font-size:16px;letter-spacing:.3px;color:var(--ink);line-height:1.2}
.brand-name small{display:block;font-size:11px;font-weight:700;letter-spacing:0}
.header-contact{position:absolute;right:146px;top:52px;text-align:right;font-family:"Raleway",sans-serif}
.header-contact a{color:var(--blue-text);font-size:16px;text-decoration:none;display:block}
.header-contact .phone{font-size:22px;color:#444;display:flex;align-items:center;gap:6px;justify-content:flex-end}
.main-nav{position:absolute;top:113px;left:0;width:1200px;height:47px;background:linear-gradient(#3a9cf0,#1b74cc)}
.main-nav ul{list-style:none;display:flex;justify-content:center;height:100%;margin-left:-12px}
.main-nav li{display:flex;align-items:center;padding:0 24px;color:var(--white);font-family:"Open Sans",sans-serif;font-size:15px;border-right:1px solid rgba(255,255,255,.25);height:100%}
.main-nav li:last-child{border-right:0}
.hero{position:absolute;top:160px;left:0;width:1200px;height:456px;overflow:hidden}
.hero-photo{position:absolute;inset:0;background:linear-gradient(90deg,#fff 0%,#fff 28%,#c9c2b6 45%,#b59a72 60%,#9a8a76 78%,#a9a398 100%)}
.hero-fade{position:absolute;left:0;right:0;bottom:0;height:120px;background:linear-gradient(transparent,rgba(235,235,235,.9))}
.hero-copy{position:absolute;left:135px;top:123px;width:420px}
.hero-copy h1{font-family:"Raleway",sans-serif;font-weight:500;font-size:33px;color:#111}
.hero-copy h2{font-family:"Raleway",sans-serif;font-weight:400;font-size:24px;color:var(--blue-text);margin-top:8px}
.hero-copy p{font-size:10px;color:var(--muted);line-height:1.8;margin-top:10px}
.dots{display:flex;gap:4px;margin-top:12px}
.dots span{width:15px;height:15px;border-radius:50%;background:#ccc}
.dots span:first-child{background:var(--blue)}
.solutions{position:absolute;top:616px;left:0;width:1200px;height:371px}
.solutions h2{position:absolute;left:142px;top:64px;font-family:"Raleway",sans-serif;font-weight:400;font-size:31px;line-height:1.35;color:#333}
.checklist{position:absolute;left:145px;top:164px;width:530px;list-style:none}
.checklist li{position:relative;padding-left:23px;font-size:11px;line-height:1.65;color:#444;margin-bottom:7px}
.checklist svg{position:absolute;left:0;top:3px}
.solutions-photo{position:absolute;left:705px;top:74px;width:330px;height:196px;background:linear-gradient(120deg,#c4312c,#e7b431 45%,#2a5fb5 75%,#d9a93a)}
.benefits{position:absolute;top:987px;left:0;width:1200px;height:311px;background:var(--blue)}
.benefits-tab{position:absolute;left:450px;top:0;width:288px;height:57px;background:#1f7dd4;clip-path:polygon(0 0,100% 0,92% 100%,8% 100%);display:flex;align-items:center;justify-content:center;color:var(--white);font-family:"Raleway",sans-serif;font-size:21px}
.benefit{position:absolute;top:127px;width:200px;text-align:center;color:var(--white)}
.benefit h3{font-family:"Raleway",sans-serif;font-weight:400;font-size:18px;margin-top:14px}
.benefit p{font-size:10px;color:rgba(255,255,255,.65);line-height:1.8;margin-top:8px}
.benefit .icon{height:42px;display:flex;justify-content:center;align-items:flex-end}
.arrow{position:absolute;top:145px}
.features{position:absolute;top:1298px;left:0;width:1200px;height:422px}
.feature{position:absolute;top:53px;width:268px}
.feature-photo{width:268px;height:138px}
.feature h3{font-family:"Raleway",sans-serif;font-weight:400;font-size:22px;margin-top:16px;color:#222}
.feature p{font-size:11px;line-height:1.65;color:#444;margin-top:6px}
.btn{display:inline-block;margin-top:16px;background:linear-gradient(#3a9cf0,#1b74cc);color:var(--white);font-size:10px;padding:7px 18px;border-radius:2px}
.products{position:absolute;top:1720px;left:0;width:1200px;height:358px;background:var(--grey-bg)}
.products-title{position:absolute;left:142px;top:44px;width:918px;display:flex;align-items:center;gap:12px;font-family:"Raleway",sans-serif;font-size:23px;color:#555}
.products-title::before,.products-title::after{content:"";flex:1;height:1px;background:var(--line)}
.product{position:absolute;top:100px;width:175px;height:205px;background:var(--white);border:1px solid #ddd;box-shadow:0 1px 3px rgba(0,0,0,.15);text-align:center}
.product-photo{width:110px;height:95px;margin:25px auto 0}
.product h4{font-family:"Raleway",sans-serif;font-weight:400;font-size:15px;color:var(--blue-text);margin-top:17px}
.product p{font-size:10px;color:#555;margin-top:3px}
.site-footer{position:absolute;top:2078px;left:0;width:1200px;height:122px;background:var(--black);color:var(--white)}
.footer-nav{position:absolute;left:148px;top:40px;font-size:13px;font-weight:600}
.footer-nav span{margin:0 5px;opacity:.8}
.copy{position:absolute;left:148px;top:72px;font-size:11px;color:#777}
.social{position:absolute;right:155px;top:37px;display:flex;gap:12px}
.social span{width:18px;height:18px;border-radius:50%;background:var(--white)}
</style>
</head>
<body>
<header class="site-header">
  <div class="brand"><span class="brand-mark"></span><div class="brand-name">MAPLEWICK HAVEN SUPPLY<small>Packaging • Printing • Distribution</small></div></div>
  <div class="header-contact">
    <a href="#contact">Contact Us</a>
    <div class="phone"><svg width="16" height="18" viewBox="0 0 16 18"><path d="M3 1l3 0 1 4-2 2c1 2 3 4 5 5l2-2 4 1 0 3c0 2-1 3-3 3C7 17 0 10 0 4 0 2 1 1 3 1z" fill="#999"/></svg>555.014.2280</div>
  </div>
</header>
<nav class="main-nav"><ul><li>HOME</li><li>ABOUT US</li><li>SERVICES</li><li>PRODUCTS</li><li>BENEFITS</li><li>SUPPORT</li><li>BLOG</li><li>CONTACT</li></ul></nav>

<section class="hero">
  <div class="hero-photo" role="img" aria-label="Cardboard boxes moving along a roller conveyor in a warehouse"></div>
  <div class="hero-fade"></div>
  <div class="hero-copy">
    <h1>Distribution &amp; Packaging</h1>
    <h2>Praesent elementum elit at tellus</h2>
    <p>In massa libero interdum nec interdum vel blandit sed nulla in ullamcorper est eget tempor cursus neque mi consectetuer mi a ultricies massa</p>
    <div class="dots"><span></span><span></span><span></span><span></span></div>
  </div>
</section>

<section class="solutions">
  <h2>Supply Chain<br>Management Solutions</h2>
  <ul class="checklist">
    <li><svg width="14" height="14" viewBox="0 0 14 14"><circle cx="7" cy="7" r="7" fill="#2a8ee8"/><path d="M3.5 7l2.3 2.3 4.7-4.7" stroke="#fff" stroke-width="1.8" fill="none"/></svg>Are your Procurement Professionals managing transactional purchases across multiple locations, departments, or business units?</li>
    <li><svg width="14" height="14" viewBox="0 0 14 14"><circle cx="7" cy="7" r="7" fill="#2a8ee8"/><path d="M3.5 7l2.3 2.3 4.7-4.7" stroke="#fff" stroke-width="1.8" fill="none"/></svg>Do you have a need to control your indirect supply spend across multiple categories and suppliers?</li>
    <li><svg width="14" height="14" viewBox="0 0 14 14"><circle cx="7" cy="7" r="7" fill="#2a8ee8"/><path d="M3.5 7l2.3 2.3 4.7-4.7" stroke="#fff" stroke-width="1.8" fill="none"/></svg>Would you like to consolidate your indirect supply purchases on one ordering platform?</li>
    <li><svg width="14" height="14" viewBox="0 0 14 14"><circle cx="7" cy="7" r="7" fill="#2a8ee8"/><path d="M3.5 7l2.3 2.3 4.7-4.7" stroke="#fff" stroke-width="1.8" fill="none"/></svg>Would you like to put the transactional ordering of “supplies” into the hands of the people that have the need, while still controlling budgets, item mix, and the ability to leverage your spend with multiple suppliers?</li>
  </ul>
  <div class="solutions-photo" role="img" aria-label="Assorted packaged grocery products"></div>
</section>

<section class="benefits">
  <div class="benefits-tab">Benefits &amp; Features</div>
  <svg class="arrow" style="left:90px" width="20" height="46" viewBox="0 0 20 46"><path d="M18 2L2 23l16 21" stroke="rgba(255,255,255,.6)" stroke-width="2" fill="none"/></svg>
  <svg class="arrow" style="left:1082px" width="20" height="46" viewBox="0 0 20 46"><path d="M2 2l16 21L2 44" stroke="rgba(255,255,255,.6)" stroke-width="2" fill="none"/></svg>
  <div class="benefit" style="left:134px"><div class="icon"><svg width="40" height="40" viewBox="0 0 40 40"><rect x="4" y="12" width="24" height="24" fill="#fff"/><circle cx="16" cy="10" r="6" fill="#fff"/><circle cx="31" cy="24" r="6" fill="#fff"/></svg></div><h3>Control your Spend</h3><p>Morbi diam mauris viverra in gravida eu mattis in ante Morbi eget arcu</p></div>
  <div class="benefit" style="left:369px"><div class="icon"><svg width="38" height="42" viewBox="0 0 38 42"><rect x="6" y="2" width="22" height="14" rx="2" fill="#fff"/><rect x="4" y="18" width="30" height="22" rx="4" fill="#fff"/></svg></div><h3>Eliminate Rogue Spend</h3><p>Morbi diam mauris viverra in gravida eu mattis in ante Morbi eget arcu</p></div>
  <div class="benefit" style="left:605px"><div class="icon"><svg width="52" height="34" viewBox="0 0 52 34"><rect x="2" y="2" width="48" height="30" fill="none" stroke="#fff" stroke-width="4"/><circle cx="26" cy="17" r="8" fill="#fff"/></svg></div><h3>Improve Cash Flow</h3><p>Morbi diam mauris viverra in gravida eu mattis in ante Morbi eget arcu</p></div>
  <div class="benefit" style="left:841px"><div class="icon"><svg width="40" height="36" viewBox="0 0 40 36"><path d="M4 34C4 18 14 12 26 12V4l12 12-12 12v-8C16 20 8 24 4 34z" fill="#fff"/></svg></div><h3>Prevent Spending Abuse</h3><p>Morbi diam mauris viverra in gravida eu mattis in ante Morbi eget arcu</p></div>
</section>

<section class="features">
  <article class="feature" style="left:141px"><div class="feature-photo" role="img" aria-label="Warehouse workers checking a parcel" style="background:linear-gradient(135deg,#6b4b32,#b98a5a 55%,#4a4440)"></div><h3>Products &amp; Service</h3><p>Curabitur iaculis tempus eros Curabitur vel mi sit amet magna malesuada ultrices Ut nisi erat fermentum vel congue id euismod in elit Fusce ultricies orci ac feugiat suscipit leo massa sodales</p><span class="btn">READ MORE</span></article>
  <article class="feature" style="left:461px"><div class="feature-photo" role="img" aria-label="Hand drawing a product management diagram" style="background:linear-gradient(135deg,#f4f4fa,#dcdcef);border:1px solid #ccc"></div><h3>MHS Web Dashboard</h3><p>Curabitur iaculis tempus eros Curabitur vel mi sit amet magna malesuada ultrices Ut nisi erat fermentum vel congue id euismod in elit Fusce ultricies orci ac feugiat suscipit leo massa sodales</p><span class="btn">READ MORE</span></article>
  <article class="feature" style="left:781px"><div class="feature-photo" role="img" aria-label="Packaging machine sealing boxes" style="background:linear-gradient(135deg,#5d6a80,#9aa3b2 50%,#7a3a3a)"></div><h3>What We Do</h3><p>Curabitur iaculis tempus eros Curabitur vel mi sit amet magna malesuada ultrices Ut nisi erat fermentum vel congue id euismod in elit Fusce ultricies orci ac feugiat suscipit leo massa sodales</p><span class="btn">READ MORE</span></article>
</section>

<section class="products">
  <h2 class="products-title">OUR PRODUCTS</h2>
  <div class="product" style="left:138px"><div class="product-photo" role="img" aria-label="Cotton mop head" style="background:linear-gradient(#e8e1cc,#cfc4a6)"></div><h4>Product Name</h4><p>Aestibulum ut commodo</p></div>
  <div class="product" style="left:325px"><div class="product-photo" role="img" aria-label="Clear plastic storage bin" style="background:linear-gradient(#f2f4f2,#d8dcd8)"></div><h4>Product Name</h4><p>Aestibulum ut commodo</p></div>
  <div class="product" style="left:512px"><div class="product-photo" role="img" aria-label="Stacked colored storage bins" style="background:linear-gradient(135deg,#d8332a,#2c5fc2 50%,#e9c92a)"></div><h4>Product Name</h4><p>Aestibulum ut commodo</p></div>
  <div class="product" style="left:699px"><div class="product-photo" role="img" aria-label="Green hanging file folder" style="background:linear-gradient(135deg,#3ea95a,#27803f)"></div><h4>Product Name</h4><p>Aestibulum ut commodo</p></div>
  <div class="product" style="left:886px"><div class="product-photo" role="img" aria-label="Assortment of cleaning supplies" style="background:linear-gradient(135deg,#3a5aa8,#c83a3a 55%,#9aa0aa)"></div><h4>Product Name</h4><p>Aestibulum ut commodo</p></div>
</section>

<footer class="site-footer">
  <div class="footer-nav">HOME<span>|</span>ABOUT US<span>|</span>SERVICES<span>|</span>PRODUCTS<span>|</span>BENEFITS<span>|</span>SUPPORT<span>|</span>BLOG<span>|</span>CONTACT</div>
  <div class="copy">© 2015 Company Name &nbsp;All right reserved &nbsp;Term of Use</div>
  <div class="social"><span></span><span></span><span></span></div>
</footer>
</body>
</html>
```